Bespoke Builders Business Card Design

We need a business card for an established builder of high quality bespoke homes in Auckland and Northland. We build and renovate homes collaboratively facilitating effective communication between owners, builders, architects, suppliers and tradespeople. We have never built or renovated a home that leaks or has faults. We only use reliable materials. We have never been sued or had legal action taken against us. We are honest builders of bespoke homes not group mass produced homes. Our niche market is in character homes. We practice sustainability and have built a lot of coastal property. We have been in business for over thirty years . We would like to see natural colors of the environment sand,sea and maybe vegetation . The design should communicate quality, sustainability,fair pricing, open communication and the originality of bespoke building. And the fact that the builder is registered.

Industry/Entity Type

Business

Contact Information for Business Card

Rowan Tellick Builders
Ph. 021583917
18 Kestrel Rd Harwood Bay Auckland 0814
PO Box 927 Mangawhai 0583

```html
<!DOCTYPE html>
<html lang="en">
<head>
<meta charset="utf-8">
<title>Rowan Tellick Builders – Business Card</title>
<link rel="stylesheet" href="https://fonts.googleapis.com/css2?family=Libre+Bodoni:wght@600&family=PT+Sans&display=swap">
<style>
  :root {
    --navy: #262262;
    --ink: #000000;
    --paper: #ffffff;
    --backdrop: #ecebe8;
    --card-w: 917px;
    --card-h: 524px;
  }
  * { box-sizing: border-box; margin: 0; padding: 0; }
  html, body {
    width: 1189px;
    height: 1200px;
    overflow: hidden;
    background: var(--backdrop);
  }
  .sheet {
    position: relative;
    width: 1189px;
    height: 1200px;
  }
  .card {
    position: absolute;
    left: 140px;
    width: var(--card-w);
    height: var(--card-h);
    overflow: hidden;
    box-shadow: 2px 4px 10px rgba(0,0,0,0.25);
  }
  .card--front { top: 45px; background: var(--paper); }
  .card--back {
    top: 624px;
    background: var(--ink);
    border: 13px solid var(--navy);
    display: flex;
    align-items: center;
    justify-content: center;
  }
  .brand-row {
    position: absolute;
    top: 94px;
    left: 0;
    right: 0;
    transform: translateY(-50%);
    display: flex;
    align-items: center;
  }
  .rule {
    flex: 1;
    height: 3px;
    background: var(--ink);
  }
  .brand-name {
    font-family: "Libre Bodoni", "Bodoni Moda", serif;
    font-weight: 600;
    color: var(--navy);
    font-size: 54px;
    line-height: 1;
    padding: 0 12px;
    white-space: nowrap;
  }
  .contact {
    position: absolute;
    top: 226px;
    left: 0;
    right: 0;
    text-align: center;
    font-family: "PT Sans", "Myriad Pro", sans-serif;
    font-size: 28px;
    line-height: 45px;
    color: var(--ink);
  }
  .swoosh {
    position: absolute;
    left: 0;
    bottom: 0;
    width: 100%;
    height: 100%;
  }
  .swoosh .band { fill: var(--navy); }
  .swoosh .stroke { fill: var(--ink); }
  .back-name {
    font-family: "Libre Bodoni", "Bodoni Moda", serif;
    font-weight: 600;
    color: var(--paper);
    font-size: 62px;
    line-height: 1;
    white-space: nowrap;
  }
</style>
</head>
<body>
<main class="sheet">
  <section class="card card--front">
    <svg class="swoosh" viewBox="0 0 1123 642" preserveAspectRatio="none" aria-hidden="true">
      <path class="stroke" d="M73 551 Q560 440 1123 522 L1123 568 Q600 470 73 551 Z"/>
      <path class="band" d="M0 582 Q560 480 1123 580 L1123 642 L0 642 Z"/>
    </svg>
    <div class="brand-row">
      <span class="rule"></span>
      <h1 class="brand-name">Rowan Tellick Builders</h1>
      <span class="rule"></span>
    </div>
    <address class="contact" style="font-style:normal">
      <p class="contact__phone">021583917</p>
      <p class="contact__street">18 Kestrel Rd Harwood Bay Auckland 0814</p>
      <p class="contact__postal">PO Box 927 Mangawhai 0583</p>
    </address>
  </section>

  <section class="card card--back">
    <h2 class="back-name">Rowan Tellick Builders</h2>
  </section>
</main>
</body>
</html>
```